Business Card Re-Design/Update

We'd like to update out business cards. I've included our current "Style guide" which has the colour scheme of the organisation in it. I've also included the branding files with logos etc in them.

I've also included a copy of one of our existing cards so that you can see how ugly/dated they look. I'd like a fresh modern corporate look.

Target Market(s)

These are for our clients, potential clients, industry contacts - like all business cards

Contact Information for Business Card

Name
Position
Company Address - Level 1, 47 Fernby Street, Carlow Qld 4072
Direct Phone
mobile
Email
Website -www.korvalit.com.au
Logo

Colors

Designer to choose colors to be used in the design.

Requirements
Must have
• Main Logo
• Cards will need to be editable to be able to personalize them for each new employee.
Nice to have
• The MapOut, ShipWell, KeepSteady would be okay to have if they can be sensibly and professionally added to the look without detracting from the main imagery.
• Maybe they could go on the back of the card? will leave this to your creative discretion as to whether/where they fit.
Should not have
• Should not have decorative or script fonts

```html
<!DOCTYPE html>
<html lang="en">
<head>
<meta charset="utf-8">
<title>korvalIT business card</title>
<link rel="stylesheet" href="https://fonts.googleapis.com/css2?family=Roboto:wght@400;500;700&family=Roboto+Condensed:wght@700&display=swap">
<style>
  :root {
    --stage: #2b2b2b;
    --card-front: #f2f2f2;
    --card-back: #231f20;
    --brand-red: #c8161d;
    --ink: #111111;
    --muted: #555555;
    --rule: #a8a8a8;
    --white: #ffffff;
    --mapout: #5e9e3c;
    --shipwell: #2b87c9;
    --keepsteady: #c1279b;
  }
  * { margin: 0; padding: 0; box-sizing: border-box; }
  html, body { width: 1200px; height: 960px; overflow: hidden; }
  body { background: var(--stage); font-family: "Roboto", Arial, sans-serif; position: relative; }

  .card { position: absolute; width: 600px; height: 342px; }
  .card--front { left: 322px; top: 108px; background: var(--card-front); }
  .card--back { left: 320px; top: 493px; background: var(--card-back); }

  .holder-name {
    position: absolute; left: 28px; top: 32px;
    font-family: "Roboto Condensed", Arial, sans-serif; font-weight: 700;
    font-size: 21px; color: var(--brand-red); letter-spacing: 0.2px;
  }
  .holder-role { position: absolute; left: 28px; top: 57px; font-size: 14px; color: var(--ink); }

  .address { position: absolute; left: 29px; top: 140px; font-size: 14.5px; line-height: 18px; color: var(--muted); width: 260px; }

  .contacts { position: absolute; left: 29px; top: 185px; list-style: none; }
  .contacts li { display: flex; align-items: center; height: 19px; font-size: 14.5px; color: var(--muted); }
  .contacts svg { width: 14px; height: 14px; margin-right: 8px; fill: var(--brand-red); flex: none; }

  .front-mark { position: absolute; left: 345px; top: 118px; display: flex; align-items: center; }
  .front-mark .mark-square { width: 34px; height: 34px; background: var(--brand-red); margin-right: 12px; }
  .front-mark .mark-name { font-weight: 700; font-size: 36px; color: var(--brand-red); letter-spacing: -0.5px; }

  .rule { position: absolute; left: 0; right: 6px; top: 302px; height: 1px; background: var(--rule); }
  .web-band {
    position: absolute; left: 326px; top: 288px; width: 238px; height: 27px;
    background: var(--brand-red); color: var(--white);
    font-size: 14px; letter-spacing: 1.6px; text-align: center; line-height: 27px;
  }

  .back-logo { position: absolute; left: 95px; top: 120px; display: flex; align-items: center; }
  .back-logo .mark-square { width: 62px; height: 62px; background: var(--brand-red); margin-right: 22px; }
  .back-logo .mark-name { font-weight: 700; font-size: 58px; color: var(--white); letter-spacing: -1px; }

  .services { position: absolute; left: 46px; top: 276px; display: flex; gap: 36px; }
  .service { display: flex; align-items: center; font-weight: 500; font-size: 26px; letter-spacing: -0.5px; }
  .service .service-square { width: 22px; height: 22px; margin-right: 8px; }
  .service--mapout { color: var(--mapout); }
  .service--mapout .service-square { background: var(--mapout); }
  .service--shipwell { color: var(--shipwell); }
  .service--shipwell .service-square { background: var(--shipwell); }
  .service--keepsteady { color: var(--keepsteady); }
  .service--keepsteady .service-square { background: var(--keepsteady); }
</style>
</head>
<body>
  <section class="card card--front">
    <h1 class="holder-name">MAREN HOLT</h1>
    <p class="holder-role">Business Development Manager</p>
    <p class="address">Level 1, 47 Fernby Street<br>Carlow Qld 4072</p>
    <ul class="contacts">
      <li><svg viewBox="0 0 16 16"><path d="M3.5 1l2.5 3-1.5 1.8c.8 1.9 2.2 3.4 4.1 4.3L10.4 8.5l3.1 2.4-1.4 3c-5.3-.4-9.6-4.8-10-10.1z"/></svg>+61 (0)7 5550 1420</li>
      <li><svg viewBox="0 0 16 16"><path d="M3.5 1l2.5 3-1.5 1.8c.8 1.9 2.2 3.4 4.1 4.3L10.4 8.5l3.1 2.4-1.4 3c-5.3-.4-9.6-4.8-10-10.1z"/></svg>+61 (0)7 5550 1436</li>
      <li><svg viewBox="0 0 16 16"><path d="M4.5 0h7a1 1 0 0 1 1 1v14a1 1 0 0 1-1 1h-7a1 1 0 0 1-1-1V1a1 1 0 0 1 1-1zm.8 2v10.5h5.4V2zM8 13.3a.9.9 0 1 0 0 1.8.9.9 0 0 0 0-1.8z"/></svg>+61 (0)400 555 218</li>
      <li><svg viewBox="0 0 16 16"><path d="M4 1h7l1.5 1.5V6H4zM1 7h14v6h-2v2H3v-2H1zm3.5 4v2.5h7V11z"/></svg>+61 (0)7 5550 1409</li>
      <li><svg viewBox="0 0 16 16"><path d="M1 3h14v1.2L8 8.6 1 4.2zm0 2.6l7 4.4 7-4.4V13H1z"/></svg>mholt@korvalit.com.au</li>
    </ul>
    <div class="front-mark"><span class="mark-square"></span><span class="mark-name">korvalIT</span></div>
    <div class="rule"></div>
    <div class="web-band">www.korvalit.com.au</div>
  </section>

  <section class="card card--back">
    <div class="back-logo"><span class="mark-square"></span><span class="mark-name">korvalIT</span></div>
    <div class="services">
      <span class="service service--mapout"><span class="service-square"></span>MapOut</span>
      <span class="service service--shipwell"><span class="service-square"></span>ShipWell</span>
      <span class="service service--keepsteady"><span class="service-square"></span>KeepSteady</span>
    </div>
  </section>
</body>
</html>
```